R7M Horizon Business Card Design

We need a business card created for our New Business "R7M Horizon"<br/><br/>The business card design is up to you however the following information must be on the business card:<br/><br/>Front of the business card -<br/>Email :darrenp@r7mhorizon.nz<br/>Mobile: +64 (0) 22 4870 619<br/>Website: www.r7mhorizon.nz<br/>Card Owner Name: Darren Paltrow<br/>Company Title: Business Development Manager<br/>Slogan: "The BEST of both worlds". <br/>Logo On the front attached to the design brief<br/><br/>On the back: <br/>Space on the back for 4 more versions of the logo across the bottom of the card indicating different subsidiary brands - R7M Coffee, R7M Arts, R7M ?? (The card will be used for all of these brands - We Will add the extra subsidiary logos to the design once the design is finished (We are a graphics design team). <br/><br/>Other than that we want a premium feeling logo that remains universally usable depending on the business entity that we are using the card for. The use of bright bold colours would be great but we still want the card to feel premium.
Target Market(s)
Gift Design and Manufacturing Companies
Contact Information for Business Card
Front of the business card -
Email :darrenp@r7mhorizon.nz
Mobile: +64 (0) 22 4870 619
Website: www.r7mhorizon.nz
Card Owner Name: Darren Paltrow
Company Title: Business Development Manager
Slogan: "The BEST of both worlds".
Logo On the front attached to the design brief

```html
<!DOCTYPE html>
<html lang="en">
<head>
<meta charset="utf-8">
<title>R7M Horizon Business Card</title>
<link href="https://fonts.googleapis.com/css2?family=Montserrat:wght@400;600&family=Quicksand:wght@700&family=Raleway:wght@400&family=PT+Sans:wght@400&display=swap" rel="stylesheet">
<style>
  :root {
    --backdrop: #c0c0c0;
    --paper: #ffffff;
    --brand-blue: #37479c;
    --ink: #2a2a2a;
    --on-blue: #ffffff;
  }
  html, body {
    margin: 0;
    padding: 0;
    width: 960px;
    height: 1200px;
    overflow: hidden;
    background: var(--backdrop);
  }
  .canvas { position: relative; width: 960px; height: 1200px; }
  .card { position: absolute; display: block; }
  .card--front { left: 224px; top: 221px; }
  .card--back { left: 220px; top: 678px; }
  .paper { fill: var(--paper); }
  .band { fill: var(--brand-blue); }
  .wordmark {
    font-family: "Montserrat", sans-serif;
    font-weight: 600;
    fill: var(--brand-blue);
  }
  .mark-dot { fill: var(--brand-blue); }
  .slogan {
    font-family: "Raleway", sans-serif;
    font-size: 19px;
    letter-spacing: 2px;
    fill: var(--on-blue);
  }
  .holder-name {
    font-family: "Quicksand", sans-serif;
    font-weight: 700;
    font-size: 28px;
    fill: var(--on-blue);
  }
  .holder-role {
    font-family: "Raleway", sans-serif;
    font-size: 18px;
    fill: var(--on-blue);
  }
  .contact-line {
    font-family: "PT Sans", sans-serif;
    font-size: 15.5px;
    fill: var(--on-blue);
  }
  .contact-icon { fill: none; stroke: var(--on-blue); stroke-width: 1.6; }
  .contact-icon--solid { fill: var(--on-blue); stroke: none; }
  .job-title {
    font-family: "Montserrat", sans-serif;
    font-size: 17px;
    fill: var(--ink);
  }
</style>
</head>
<body>
<main class="canvas">

  <!-- Card: logo side -->
  <svg class="card card--front" width="509" height="290" viewBox="0 0 636 363" aria-label="Business card, logo side">
    <defs>
      <clipPath id="front-shape"><rect width="636" height="363" rx="12"/></clipPath>
    </defs>
    <g clip-path="url(#front-shape)">
      <rect class="paper" width="636" height="363"/>
      <path class="band" d="M0,252 H334 Q334,229 357,229 H636 V363 H0 Z"/>
    </g>
    <g class="brand-lockup">
      <circle class="mark-dot" cx="168" cy="124" r="15"/>
      <text class="wordmark" x="196" y="143" font-size="52">R7M Horizon</text>
    </g>
    <text class="slogan" x="322" y="339" text-anchor="middle">"The BEST of both worlds"</text>
  </svg>

  <!-- Card: contact side -->
  <svg class="card card--back" width="509" height="290" viewBox="0 0 636 363" aria-label="Business card, contact side">
    <defs>
      <clipPath id="back-shape"><rect width="636" height="363" rx="12"/></clipPath>
    </defs>
    <g clip-path="url(#back-shape)">
      <rect class="paper" width="636" height="363"/>
      <path class="band" d="M305,0 H636 V363 H350 Q350,338 328,318 Q305,298 305,262 Z"/>
    </g>

    <g class="brand-lockup">
      <circle class="mark-dot" cx="40" cy="176" r="9"/>
      <text class="wordmark" x="56" y="188" font-size="32">R7M Horizon</text>
    </g>

    <text class="holder-name" x="321" y="63">Darren Paltrow</text>
    <text class="holder-role" x="321" y="89">Owner</text>

    <g class="contact-list">
      <path class="contact-icon" d="M320,160 q-2,6 4,14 q6,8 12,6 l2,-3 l-4,-3 l-2,2 q-4,-2 -7,-8 l2,-2 l-3,-4 Z"/>
      <text class="contact-line" x="351" y="169">+64 (0) 22 4870 619</text>

      <path class="contact-icon--solid" d="M319,199 L327,194 L335,199 V209 H319 Z"/>
      <path d="M319,199 L327,205 L335,199" fill="none" stroke="#37479c" stroke-width="1.4"/>
      <text class="contact-line" x="351" y="206">darrenp@r7mhorizon.nz</text>

      <g class="contact-icon">
        <circle cx="327" cy="238" r="8"/>
        <ellipse cx="327" cy="238" rx="3.5" ry="8"/>
        <line x1="319" y1="238" x2="335" y2="238"/>
      </g>
      <text class="contact-line" x="353" y="240">www.r7mhorizon.nz</text>
    </g>

    <text class="job-title" x="21" y="347">Business Development Manager</text>
  </svg>

</main>
</body>
</html>
```